Oriel Photography Business Card

I need a business card designed for a photography business based in Perth, Western Australia called Oriel Photography.

We specialise in wedding, event photography and portrait photography.

The business card must borrow the style of the attached logo.

The hex codes for the colours in the logo are:
#ED1D85 - Pink
#89C23E - Green
#37282F - Black

The name on the card will be:
Name: Tobrian
Phone: 0417395268
Website: www.orielphotography.example.com.au
Facebook: orielphotography

I am open and happy to accept creative concepts.

I’d like some space at the back for writing notes and appointment details.

```html
<!DOCTYPE html>
<html lang="en">
<head>
<meta charset="utf-8">
<title>Oriel Photography Business Card</title>
<link href="https://fonts.googleapis.com/css2?family=Cinzel:wght@400&family=Open+Sans:ital,wght@0,400;0,600;0,700;1,400&display=swap" rel="stylesheet">
<style>
  :root {
    --pink: #ED1D85;
    --green: #89C23E;
    --ink: #37282F;
    --band: #4a383f;
    --grey: #555;
    --line: #9a9a9a;
    --paper: #ffffff;
    --backdrop: #e6e6ec;
  }
  * { box-sizing: border-box; margin: 0; padding: 0; }
  html, body { width: 1200px; height: 987px; overflow: hidden; }
  body {
    background: var(--backdrop);
    font-family: "Open Sans", Arial, sans-serif;
    color: var(--ink);
    position: relative;
  }
  .card {
    position: absolute;
    left: 250px;
    width: 700px;
    height: 400px;
    background: var(--paper);
    border-radius: 24px;
    overflow: hidden;
    box-shadow: 0 6px 18px rgba(0,0,0,.12);
  }
  .card--front { top: 60px; }
  .card--back { top: 527px; }

  /* front */
  .front-bands { position: absolute; inset: 0; }
  .holder-name {
    position: absolute; right: 60px; top: 190px;
    color: #fff; font-weight: 700; font-size: 30px; letter-spacing: 1px;
  }
  .brand {
    position: absolute; left: 40px; top: 182px;
    display: flex; align-items: center; gap: 12px;
  }
  .brand-dot { width: 20px; height: 20px; border-radius: 50%; background: var(--pink); flex: none; }
  .brand-name {
    font-size: 16px; letter-spacing: 7px; text-transform: uppercase; color: var(--ink);
    white-space: nowrap;
  }
  .contacts { position: absolute; left: 40px; top: 240px; list-style: none; }
  .contacts li {
    display: flex; align-items: center; gap: 10px;
    font-size: 17px; color: var(--ink); margin-bottom: 7px;
  }
  .contacts svg { width: 16px; height: 16px; flex: none; }
  .watermark {
    position: absolute; left: 250px; top: 358px;
    font-size: 21px; color: var(--pink); opacity: .14; letter-spacing: 3px;
    text-transform: uppercase; white-space: nowrap;
  }

  /* back */
  .appt-title {
    position: absolute; left: 50px; top: 34px;
    font-family: "Cinzel", Georgia, serif; color: var(--pink); font-size: 24px;
  }
  .field {
    position: absolute; display: flex; align-items: flex-end; gap: 10px;
    font-size: 17px; color: var(--grey); white-space: nowrap;
  }
  .field .rule { border-bottom: 1px dotted var(--line); height: 1px; }
  .field--name { left: 50px; top: 84px; }
  .field--date { left: 50px; top: 120px; }
  .field--next { left: 50px; top: 170px; align-items: center; }
  .box { border: 1.5px solid #888; border-radius: 4px; background: #fff; }
  .field--time { left: 360px; top: 120px; }
  .field--time-box { left: 360px; top: 170px; align-items: center; }
  .days {
    position: absolute; left: 50px; top: 240px;
    display: flex; gap: 18px; list-style: none;
  }
  .days li {
    display: flex; align-items: center; gap: 8px;
    font-weight: 700; font-size: 17px; color: var(--grey);
  }
  .days .box { width: 40px; height: 28px; }
  .note {
    position: absolute; left: 50px; top: 300px;
    font-style: italic; font-size: 17px; color: var(--grey);
  }
  .back-brand {
    position: absolute; right: 40px; top: 330px;
    display: flex; align-items: center; gap: 10px;
    font-size: 15px; color: var(--pink); letter-spacing: 3px; text-transform: uppercase;
  }
  .back-brand .brand-dot { width: 16px; height: 16px; }
</style>
</head>
<body>

<section class="card card--front" aria-label="Business card front">
  <svg class="front-bands" viewBox="0 0 700 400" width="700" height="400" aria-hidden="true">
    <path d="M0,0 H700 V400 H610 C560,250 380,90 0,42 Z" fill="var(--band)"/>
    <path d="M0,42 C380,90 560,250 610,400 H582 C532,262 372,102 0,53 Z" fill="var(--green)"/>
    <path d="M0,62 C120,70 230,86 300,108 C220,92 120,78 0,67 Z" fill="var(--band)"/>
  </svg>
  <div class="holder-name">TOBRIAN</div>
  <div class="brand">
    <span class="brand-dot"></span>
    <span class="brand-name">Oriel Photography</span>
  </div>
  <ul class="contacts">
    <li>
      <svg viewBox="0 0 16 16"><circle cx="8" cy="8" r="8" fill="var(--green)"/><path d="M5 4.5c.6-.5 1.2-.3 1.5.3l.6 1.2c.2.4 0 .8-.3 1l-.5.4c.4.9 1.1 1.7 2 2.1l.4-.5c.3-.3.7-.4 1-.2l1.2.6c.6.3.7 1 .3 1.5-.7.8-1.7.8-2.7.3C6.6 10.3 5.4 9 4.8 7.3c-.4-1-.4-2 .2-2.8z" fill="#fff"/></svg>
      0417395268
    </li>
    <li>
      <svg viewBox="0 0 16 16"><rect width="16" height="16" rx="2" fill="var(--ink)"/></svg>
      orielphotography
    </li>
    <li>
      <svg viewBox="0 0 16 16"><circle cx="8" cy="8" r="8" fill="var(--green)"/></svg>
      www.orielphotography.example.com.au
    </li>
  </ul>
  <div class="watermark">Oriel Photography</div>
</section>

<section class="card card--back" aria-label="Business card back, appointment">
  <h2 class="appt-title">YOUR APPOINTMENT</h2>
  <div class="field field--name">Name :<span class="rule" style="width:520px"></span></div>
  <div class="field field--date">Date :<span class="rule" style="width:230px"></span></div>
  <div class="field field--time">Time :<span class="rule" style="width:170px"></span>am / pm</div>
  <div class="field field--next">Next Appointment<span class="box" style="width:150px;height:34px"></span></div>
  <div class="field field--time-box"><span class="box" style="width:150px;height:34px"></span></div>
  <ul class="days">
    <li>MON <span class="box"></span></li>
    <li>TUE <span class="box"></span></li>
    <li>WED <span class="box"></span></li>
    <li>THU <span class="box"></span></li>
    <li>FRI <span class="box"></span></li>
    <li>SAT <span class="box"></span></li>
  </ul>
  <p class="note">We appreciate a 24 hr. notice for cancellations</p>
  <div class="back-brand"><span class="brand-dot"></span>Oriel Photography</div>
</section>

</body>
</html>
```